Social Media Graphics - Oakline Push REVISED

Create 6-7 individual social media graphics (square size) to encourage folks to join our online course called:

The Harvest Ledger Circle
How to Launch a Multi-Million Business From Scratch
Sign Up Today!

IMPORTANT: Make the largest and most prominent text on the graphic be: How to Launch a Multi-Million Business From Scratch

For the color scheme of the graphics, let's try a blue color palette; make sure the graphics appeal to both men and women

Make sure each graphic contains 1 of the 3 pics attached (crop pic as needed); and make sure one of the graphics is all TEXT only.

Target Market(s)

men and women looking to start a business

Industry/Entity Type

Entrepreneurship

Colors
0054AA
0677BA
7BADD7
CADEEF
E8F1F8

Requirements
Must have
• All the text and use the 3 pics provided; one graphic can be all text; Simple, modern design that's easy to read

```html
<!DOCTYPE html>
<html lang="en">
<head>
<meta charset="utf-8">
<title>Oakline Push – The Harvest Ledger Circle social set</title>
<link rel="stylesheet" href="https://fonts.googleapis.com/css2?family=Archivo:wdth,wght@125,700;125,800;125,900&display=swap">
<style>
  :root {
    --canvas: #161d2e;
    --blue-deep: #0054aa;
    --blue-mid: #0677ba;
    --blue-soft: #7badd7;
    --blue-pale: #cadeef;
    --blue-mist: #e8f1f8;
    --navy-line: #0b1a3a;
    --white: #ffffff;
  }
  * { box-sizing: border-box; margin: 0; padding: 0; }
  html, body { width: 1200px; height: 400px; overflow: hidden; background: var(--canvas); }
  body { font-family: "Archivo", "Arial Black", sans-serif; font-stretch: 125%; }

  .graphic-set { position: relative; width: 1200px; height: 400px; }

  .post {
    position: absolute; top: 9px; width: 382px; height: 382px; overflow: hidden;
    background: radial-gradient(ellipse at 50% 60%, #0a6cc4 0%, var(--blue-deep) 80%);
  }
  .post--one { left: 17px; }
  .post--two { left: 409px; }
  .post--three { left: 801px; }

  .post__frame {
    position: absolute; inset: 5px; border-radius: 17px;
    border: 1.5px solid rgba(202, 222, 239, 0.5); z-index: 3;
  }

  .post__photo {
    position: absolute; left: 6px; right: 6px; top: 6px; height: 250px;
    border-radius: 16px 16px 0 0;
    -webkit-mask-image: linear-gradient(to bottom, #000 0%, #000 62%, transparent 92%);
            mask-image: linear-gradient(to bottom, #000 0%, #000 62%, transparent 92%);
  }
  .post--one .post__photo {
    background: linear-gradient(100deg, #0a5fb2 0%, #121a2a 22%, #161f30 48%, #1f3f78 58%, #24569e 78%, #0a64b8 100%);
  }
  .post--two .post__photo {
    background: linear-gradient(180deg, #6f9fcf 0%, var(--blue-pale) 14%, var(--blue-mist) 32%, var(--blue-pale) 55%, var(--blue-soft) 75%, var(--blue-mid) 100%);
  }
  .post--three .post__photo {
    background: linear-gradient(100deg, #0a64b8 0%, #c23a72 22%, #b8346a 42%, #2a2d38 58%, #22262f 80%, #0a5fb2 100%);
  }

  .post__title {
    position: absolute; left: 0; right: 0; top: 218px; z-index: 2;
    text-align: center; color: var(--white); font-weight: 900; text-transform: uppercase;
  }
  .post__title-top { display: block; font-size: 20px; line-height: 22px; letter-spacing: -0.2px; }
  .post__title-bottom { display: block; font-size: 29px; line-height: 26px; letter-spacing: 0.5px; }

  .post__headline {
    position: absolute; left: 20px; top: 265px; width: 347px; height: 83px; z-index: 2;
    border: 2.5px solid var(--navy-line); border-radius: 5px;
    background: var(--blue-deep);
    display: flex; flex-direction: column; justify-content: center; align-items: center;
    color: var(--white); font-weight: 900; text-transform: uppercase;
    font-size: 24px; line-height: 24px; text-align: center; letter-spacing: -0.9px;
  }
  .post__headline span { display: block; white-space: nowrap; }

  .post__cta {
    position: absolute; left: 0; right: 0; top: 353px; z-index: 2;
    text-align: center; color: var(--white); font-weight: 800;
    font-size: 11px; text-transform: uppercase; letter-spacing: -0.1px;
  }
</style>
</head>
<body>
<main class="graphic-set">

  <article class="post post--one">
    <div class="post__photo" role="img" aria-label="Photo of the two course hosts standing together, smiling, against a blue backdrop"></div>
    <h2 class="post__title"><span class="post__title-top">The Harvest Ledger</span><span class="post__title-bottom">Circle</span></h2>
    <p class="post__headline"><span>How to Launch a</span><span>Multi-Million Business</span><span>From Scratch</span></p>
    <p class="post__cta">Sign Up Today!</p>
    <div class="post__frame"></div>
  </article>

  <article class="post post--two">
    <div class="post__photo" role="img" aria-label="Photo of the two course hosts speaking on a bright stage by large windows"></div>
    <h2 class="post__title"><span class="post__title-top">The Harvest Ledger</span><span class="post__title-bottom">Circle</span></h2>
    <p class="post__headline"><span>How to Launch a</span><span>Multi-Million Business</span><span>From Scratch</span></p>
    <p class="post__cta">Sign Up Today!</p>
    <div class="post__frame"></div>
  </article>

  <article class="post post--three">
    <div class="post__photo" role="img" aria-label="Photo of the two course hosts posing side by side, smiling, in casual outfits"></div>
    <h2 class="post__title"><span class="post__title-top">The Harvest Ledger</span><span class="post__title-bottom">Circle</span></h2>
    <p class="post__headline"><span>How to Launch a</span><span>Multi-Million Business</span><span>From Scratch</span></p>
    <p class="post__cta">Sign Up Today!</p>
    <div class="post__frame"></div>
  </article>

</main>
</body>
</html>
```